Business Card Design - ChoiceCraft

Looking for creative, modern design, two sided for ChoiceCraft that is consistent with color and feel of website www.choicecraftpro.net.
Updates

Back of card will be used to promote products or have a quote revolving around decisions, change, leadership, innovation, creativity. Back should also have space to promote website, but optional to use the icon. Front of the card will need to use the icon and have standard place for name, job title, phone and email. We are not looking to put a mailing address or fax. Also want space to place a few words/phrase explaining what we do...such as individual growth and organizational development or tools, training, information...in addition, want the facebook icon small on the front somewhere as we are also on facebook.

Vector file uploaded of icon.

Target Market(s)

Professional coaching for individual growth and organizational development

Industry/Entity Type

Business

Requirements
Must have
• Icon...see attached.

```html
<!DOCTYPE html>
<html lang="en">
<head>
<meta charset="utf-8">
<title>ChoiceCraft Business Card</title>
<link href="https://fonts.googleapis.com/css2?family=PT+Sans:wght@400;700&family=Arimo:wght@400;700&display=swap" rel="stylesheet">
<style>
  :root {
    --stage: #262626;
    --card: #ffffff;
    --ink: #4a4a4a;
    --ink-soft: #6b6b6b;
    --brand-blue: #1e8fd0;
    --brand-light: #a9c9e6;
    --steel: #b8c2cf;
    --quote-ink: #2e2e2e;
  }
  * { box-sizing: border-box; margin: 0; padding: 0; }
  html, body { width: 1200px; height: 757px; overflow: hidden; background: var(--stage); }
  .stage {
    width: 1200px; height: 757px; position: relative;
    display: flex; align-items: center; justify-content: center; gap: 40px;
  }
  .card {
    width: 540px; height: 310px; background: var(--card);
    position: relative; overflow: hidden;
    box-shadow: 0 10px 30px rgba(0,0,0,.5);
  }

  /* Front */
  .front { font-family: "PT Sans", sans-serif; }
  .front .top-band {
    position: absolute; top: 0; right: 0; width: 300px; height: 10px;
    background: linear-gradient(90deg, var(--steel), #e4e9ef 70%, var(--brand-blue) 70%);
  }
  .front .side-band {
    position: absolute; left: 0; bottom: 0; width: 6px; height: 42px;
    background: linear-gradient(180deg, #dfe6ee, var(--brand-blue));
  }
  .brand {
    position: absolute; left: 48px; top: 98px; width: 150px;
    display: flex; flex-direction: column; align-items: center; gap: 12px;
  }
  .brand-dot { width: 64px; height: 64px; border-radius: 50%; background: var(--brand-blue); }
  .brand-name { font-size: 21px; color: var(--quote-ink); font-weight: 400; }
  .divider {
    position: absolute; left: 222px; top: 64px; width: 2px; height: 140px;
    background: linear-gradient(180deg, transparent, #9a9a9a 40%, transparent);
  }
  .identity { position: absolute; left: 244px; top: 60px; color: var(--ink); }
  .identity .name { font-size: 23px; font-weight: 700; }
  .identity .title { font-size: 15px; color: var(--ink-soft); margin: 2px 0 12px; }
  .contact { list-style: none; font-size: 14px; line-height: 18px; }
  .contact li { display: flex; align-items: center; gap: 6px; }
  .contact svg { width: 11px; height: 11px; fill: var(--quote-ink); flex: none; }
  .contact .mark { width: 10px; height: 10px; background: var(--brand-blue); flex: none; }
  .tagline {
    position: absolute; left: 0; right: 0; bottom: 34px; text-align: center;
    font-size: 16px; line-height: 20px; color: var(--ink-soft);
  }

  /* Back */
  .back { font-family: "Arimo", sans-serif; padding: 34px 36px; }
  .quotes { list-style: none; display: flex; flex-direction: column; gap: 8px; }
  .quote p { font-size: 14px; color: var(--quote-ink); position: relative; padding-left: 14px; }
  .quote p::before {
    content: "\201C"; position: absolute; left: 0; top: -4px;
    font-size: 20px; font-weight: 700; color: var(--quote-ink);
  }
  .quote p::after { content: "\201D"; font-size: 20px; font-weight: 700; line-height: 0; vertical-align: -6px; margin-left: 2px; }
  .quote cite { display: block; font-style: normal; font-size: 14px; color: var(--ink); padding-left: 20px; }
  .quote cite b { color: var(--brand-blue); }
</style>
</head>
<body>
<main class="stage">
  <section class="card front" aria-label="Card front">
    <div class="top-band"></div>
    <div class="side-band"></div>
    <div class="brand">
      <span class="brand-dot"></span>
      <span class="brand-name">ChoiceCraft</span>
    </div>
    <div class="divider"></div>
    <div class="identity">
      <h1 class="name">Your Name</h1>
      <p class="title">Title</p>
      <ul class="contact">
        <li><svg viewBox="0 0 24 24"><path d="M6.6 10.8a15 15 0 0 0 6.6 6.6l2.2-2.2a1 1 0 0 1 1-.25 11.4 11.4 0 0 0 3.6.57 1 1 0 0 1 1 1V20a1 1 0 0 1-1 1A17 17 0 0 1 3 4a1 1 0 0 1 1-1h3.5a1 1 0 0 1 1 1c0 1.25.2 2.45.57 3.57a1 1 0 0 1-.25 1z"/></svg>123-456-789</li>
        <li><svg viewBox="0 0 24 24"><path d="M2 5h20v14H2zm2 2v.5l8 5 8-5V7l-8 5z"/></svg>info@choicecraftpro.net</li>
        <li><svg viewBox="0 0 24 24"><path d="M12 2a10 10 0 1 0 0 20 10 10 0 0 0 0-20zm0 2c.9 1.2 1.6 2.7 1.9 4h-3.8c.3-1.3 1-2.8 1.9-4zM4.3 14a8 8 0 0 1 0-4h3.4a16 16 0 0 0 0 4zm.8 2h3c.3 1.3.8 2.5 1.4 3.6A8 8 0 0 1 5.1 16zm3-8h-3a8 8 0 0 1 4.4-3.6C8.9 5.5 8.4 6.7 8.1 8zM12 20c-.9-1.2-1.6-2.7-1.9-4h3.8c-.3 1.3-1 2.8-1.9 4zm2.3-6H9.7a14 14 0 0 1 0-4h4.6a14 14 0 0 1 0 4zm.2 5.6c.6-1.1 1.1-2.3 1.4-3.6h3a8 8 0 0 1-4.4 3.6zm1.8-5.6a16 16 0 0 0 0-4h3.4a8 8 0 0 1 0 4zm-.4-6c-.3-1.3-.8-2.5-1.4-3.6A8 8 0 0 1 18.9 8z"/></svg>www.choicecraftpro.net</li>
        <li><span class="mark"></span>/choicecraftpro</li>
      </ul>
    </div>
    <p class="tagline">Supporting individual growth and organizational<br>development or tools, training, information</p>
  </section>

  <section class="card back" aria-label="Card back">
    <ul class="quotes">
      <li class="quote"><p>Try not to become a man of success, but rather a man of value.</p><cite>- <b>Arlen Whitcombe</b></cite></li>
      <li class="quote"><p>The only constant is change.</p><cite>- <b>Doran Velis</b></cite></li>
      <li class="quote"><p>We are what we repeatedly do. Excellence is not an act, it is a habit.</p><cite>- <b>Marek Solari</b></cite></li>
      <li class="quote"><p>Simplicity is the ultimate sophistication.</p><cite>- <b>Lucian Ferretto</b></cite></li>
      <li class="quote"><p>Life is not fair - get used to it.</p><cite>- <b>Brent Hollis</b></cite></li>
    </ul>
  </section>
</main>
</body>
</html>
```